Talvane Aerial webdesign: Innovative Drones service company in agriculture

We need a new website according the following conditions:
• Main colour orange and current logo;
• Transparent – open – trustworthy – dynamic - personal;
• Use the smartness and overview characteristics of the crow (Talvane is Latin for crow);
• Accessible to multiple target groups and markets:
o So not too horticultural, too green;
• Use contradictions:
o Future versus nostalgia;
o Smartness crow versus precision hummingbird;
o Technology versus mechanical;
• Kestrand 2.4 LTX as a style icon?
• Long pager website
Updates

Website menu o Home o Crop monitoring  Applications Growth | Stress | Development | Diseases  Markets Breeding | Young plant | Potplants | Cutflowers | Vegetables | Soft fruit  Customer cases o Technology Aerial data collection | Artificial intelligence | Free data sets o About Vision | Company | Partners | Team | Career o Contact o News&downloads Logo: www.talvaneaerial-example.com

Target Market(s)

agriculture: owners, crop managers
oil&gas: maintenance, quality control managers and purchase managers
logistics: ware house managers, purchase managers

Industry/Entity Type

Agribusiness

Number of Pages Required

2 page

Colors
f78f20

Requirements
Must have
• long pager website
downloads
plain circle
Should not have
• Not too 'green' because first impression of designers of agriculture/horticulture is using the green colour. But that is not necessary.

Keep in mind that the current logo will be updates: the circle will be more 'general' and less 'agri'. Also the green colors in the logo will be slightly darker to make it more powerful.

```html
<!DOCTYPE html>
<html lang="en">
<head>
<meta charset="utf-8">
<title>Talvane Aerial – Customer Cases &amp; News</title>
<link rel="stylesheet" href="https://fonts.googleapis.com/css2?family=Lato:wght@300;400;700&family=Nunito+Sans:wght@300;400;700&display=swap">
<style>
:root{
  --orange:#f78f20;
  --text:#555555;
  --dark:#333333;
  --muted:#777777;
  --line:#555555;
  --band:#efefef;
  --field:#d6d4d5;
  --footer:#656565;
  --white:#ffffff;
}
*{box-sizing:border-box;margin:0;padding:0}
html,body{width:1200px;height:2500px;overflow:hidden;background:var(--white)}
body{position:relative;font-family:'Lato',sans-serif;color:var(--text)}
.abs{position:absolute}

.brand{left:62px;top:30px;display:flex;align-items:center;gap:10px}
.brand-dot{width:44px;height:44px;border-radius:50%;background:var(--orange)}
.brand-name{font-family:'Lato',sans-serif;font-weight:400;font-size:27px;color:var(--orange);letter-spacing:1px}

.main-nav{top:46px;left:0;width:1200px;height:20px}
.main-nav a{position:absolute;font-size:12.5px;color:var(--dark);text-decoration:none;letter-spacing:.1px}

.section-title{font-weight:300;font-size:38px;color:var(--orange);left:138px}

.card{left:132px;width:680px;height:178px}
.card-media{position:absolute;left:0;top:0;width:175px;height:175px;border:1.5px solid var(--orange)}
.card-title{position:absolute;left:198px;top:-6px;font-size:22px;color:var(--dark);font-weight:400;white-space:nowrap}
.card-date{position:absolute;left:198px;top:40px;font-size:15px;font-weight:700;color:var(--dark)}
.card-text{position:absolute;left:198px;top:58px;width:470px;font-size:14.8px;line-height:18px;font-weight:300;color:var(--text)}
.btn{position:absolute;display:flex;align-items:center;justify-content:center;width:133px;height:35px;border:2px solid var(--line);border-radius:18px;font-size:12.5px;color:var(--dark);background:var(--white);text-decoration:none}
.card .btn{left:200px;top:141px}

.divider{left:61px;top:1579px;width:1065px;height:1px;background:var(--line)}

.contact-band{left:64px;top:1602px;width:1065px;height:213px;background:var(--band)}
.contact-info{position:absolute;left:45px;top:16px;font-size:17px;line-height:25.5px;color:#444}
.map{position:absolute;left:570px;top:0;width:495px;height:213px;background:linear-gradient(135deg,#e6e7e3,#dcdedb 60%,#e8eae4)}

.mind-title{left:133px;top:1846px;font-family:'Nunito Sans',sans-serif;font-weight:300;font-size:40px;color:var(--orange);letter-spacing:2px}
.mind-text{left:135px;top:1918px;width:340px;font-family:'Nunito Sans',sans-serif;font-weight:300;font-size:18.5px;line-height:22.5px;color:var(--muted);letter-spacing:.5px}
.mind-text p+p{margin-top:22px}

.form-label{width:150px;text-align:right;left:443px;font-size:18px;font-weight:300;color:var(--muted)}
.field{left:636px;width:310px;height:21px;background:var(--field)}
.field-message{height:61px}

.site-footer{left:62px;top:2191px;width:1067px;height:309px;background:var(--footer);color:var(--white);font-family:'Nunito Sans',sans-serif;letter-spacing:.6px}
.site-footer h3{position:absolute;font-size:18.5px;font-weight:700;letter-spacing:1.2px}
.site-footer ul{position:absolute;list-style:none;font-size:15px;line-height:18px}
.visit{position:absolute;left:77px;top:70px;font-size:15px;line-height:18px}
.social{position:absolute;left:85px;top:150px;width:40px;height:40px;border-radius:50%;background:var(--white)}
</style>
</head>
<body>

<header>
  <div class="abs brand">
    <span class="brand-dot"></span>
    <span class="brand-name">TALVANE</span>
  </div>
  <nav class="abs main-nav">
    <a style="left:281px">HOME</a>
    <a style="left:348px">CROP MONITORING</a>
    <a style="left:505px">MARKETS</a>
    <a style="left:595px">CUSTOMER CASES</a>
    <a style="left:730px">TECHNOLOGY</a>
    <a style="left:842px">ABOUT</a>
    <a style="left:909px">CONTACTS</a>
    <a style="left:999px">NEW &amp; DOWNLOADS</a>
  </nav>
</header>

<h2 class="abs section-title" style="top:148px">Customer Cases</h2>

<article class="abs card" style="top:219px">
  <div class="card-media" role="img" aria-label="Seedlings in peat pots held on a hand" style="background:linear-gradient(180deg,#e9ece6 0%,#6b4a32 35%,#4a3322 65%,#c98a5a 100%)"></div>
  <h3 class="card-title">Lorem Ipsum set dolor consectatur</h3>
  <p class="card-date">July 30, 2020</p>
  <p class="card-text">The Talvane Aerial uses a smart navigation system in order to fly complete autonomous. The drone is equipped with camera’s and other sensors. Depending on the application this is an RGB camera or a multi-spectral camera. Other sensors can be temperature, light and CO2.</p>
  <a class="btn">READ MORE</a>
</article>

<article class="abs card" style="top:423px">
  <div class="card-media" role="img" aria-label="Young plants in tubes handled with tweezers" style="background:linear-gradient(135deg,#c9d7a6,#6f9b3c 45%,#e4e6de 100%)"></div>
  <h3 class="card-title">Lorem Ipsum set dolor consectatur</h3>
  <p class="card-date">July 30, 2020</p>
  <p class="card-text">The Talvane Aerial uses a smart navigation system in order to fly complete autonomous. The drone is equipped with camera’s and other sensors. Depending on the application this is an RGB camera or a multi-spectral camera. Other sensors can be temperature, light and CO2.</p>
  <a class="btn">READ MORE</a>
</article>

<article class="abs card" style="top:635px">
  <div class="card-media" role="img" aria-label="Purple lupins beside a pink lily flower" style="background:linear-gradient(90deg,#4b5a37 0%,#8a5d98 40%,#e79aa0 65%,#c06478 100%)"></div>
  <h3 class="card-title">Latest Aerial Data sets now available</h3>
  <p class="card-date">July 30, 2020</p>
  <p class="card-text">The Talvane Aerial uses a smart navigation system in order to fly complete autonomous. The drone is equipped with camera’s and other sensors. Depending on the application this is an RGB camera or a multi-spectral camera. Other sensors can be temperature, light and CO2.</p>
  <a class="btn">READ MORE</a>
</article>

<h2 class="abs section-title" style="top:849px">News &amp; Download</h2>

<article class="abs card" style="top:920px">
  <div class="card-media" role="img" aria-label="Front of an orange classic coupe" style="background:linear-gradient(160deg,#e8e8e8 0%,#f26a26 35%,#e85a1c 70%,#3a3a3a 100%)"></div>
  <h3 class="card-title">Lorem Ipsum set dolor consectatur</h3>
  <p class="card-date">July 30, 2020</p>
  <p class="card-text">The Talvane Aerial uses a smart navigation system in order to fly complete autonomous. The drone is equipped with camera’s and other sensors. Depending on the application this is an RGB camera or a multi-spectral camera. Other sensors can be temperature, light and CO2.</p>
  <a class="btn">READ MORE</a>
</article>

<article class="abs card" style="top:1124px">
  <div class="card-media" role="img" aria-label="Drone with orange arms standing on grass" style="background:linear-gradient(180deg,#5f9a3a 0%,#7bb04e 50%,#4f8a2f 100%)"></div>
  <h3 class="card-title">Lorem Ipsum set dolor consectatur</h3>
  <p class="card-date">July 30, 2020</p>
  <p class="card-text">The Talvane Aerial uses a smart navigation system in order to fly complete autonomous. The drone is equipped with camera’s and other sensors. Depending on the application this is an RGB camera or a multi-spectral camera. Other sensors can be temperature, light and CO2.</p>
  <a class="btn">READ MORE</a>
</article>

<article class="abs card" style="top:1336px">
  <div class="card-media" role="img" aria-label="Glowing yellow data bar visual" style="background:linear-gradient(180deg,#d8b21c 0%,#b58a1a 45%,#7a4a2a 75%,#5c3a6e 100%)"></div>
  <h3 class="card-title">Latest Aerial Data sets now available</h3>
  <p class="card-date">July 30, 2020</p>
  <p class="card-text">The Talvane Aerial uses a smart navigation system in order to fly complete autonomous. The drone is equipped with camera’s and other sensors. Depending on the application this is an RGB camera or a multi-spectral camera. Other sensors can be temperature, light and CO2.</p>
  <a class="btn">DOWNLOAD NOW</a>
</article>

<div class="abs divider"></div>

<section class="abs contact-band">
  <div class="contact-info">
    Address:<br>
    Address: Veldspaatlaan 14B, 6702KL, Ede<br>
    Email: info@talvaneaerial-example.com<br>
    Telephone: +31 6 12004587
  </div>
  <div class="map" role="img" aria-label="Street map of the office location in Ede"></div>
</section>

<h2 class="abs mind-title">What’s on your mind?</h2>
<div class="abs mind-text">
  <p>Curabitur ornare vitae sem nec tempus. Morbi laoreet metus neque, eu hendrerit magna interdum a. Aliquam erat volutpat. Nam auctor ut augue eu varius.</p>
  <p>Cras elementum accumsan pellen-tesque. Mauris nec nisi id ante faucibus consectetur. Aenean ornare aliquet neque, a fermentum odio vulputate sed.</p>
</div>

<form>
  <label class="abs form-label" style="top:1921px">Email</label>
  <label class="abs form-label" style="top:1951px">First Name</label>
  <label class="abs form-label" style="top:1981px">Last Name</label>
  <label class="abs form-label" style="top:2011px">Message</label>
  <div class="abs field" style="top:1926px"></div>
  <div class="abs field" style="top:1953px"></div>
  <div class="abs field" style="top:1980px"></div>
  <div class="abs field field-message" style="top:2008px"></div>
  <a class="btn" style="left:640px;top:2098px">SEND</a>
</form>

<footer class="abs site-footer">
  <h3 style="left:77px;top:18px">WHY DON’T YOU DROP BY?</h3>
  <p class="visit">Veldspaatlaan 14B,<br>6702KL, Ede<br>Email: info@talvaneaerial-example.com<br>Telephone: +31 6 12004587</p>
  <span class="social" role="img" aria-label="Professional network profile"></span>

  <h3 style="left:417px;top:16px">CROP MONITORING</h3>
  <ul style="left:417px;top:39px"><li>Growth</li><li>Stress</li><li>Development</li><li>Diseases</li></ul>

  <h3 style="left:627px;top:16px">TECHNOLOGY</h3>
  <ul style="left:627px;top:39px"><li>Aerial data collection</li><li>Artificial intelligence</li><li>Free data sets</li></ul>

  <h3 style="left:867px;top:16px">ABOUT</h3>
  <ul style="left:867px;top:39px"><li>Vision</li><li>Company</li><li>Partners</li><li>Team</li><li>Career</li></ul>

  <h3 style="left:417px;top:141px">MARKETS</h3>
  <ul style="left:417px;top:164px"><li>Breeding</li><li>Young plant</li><li>Potplants</li><li>Cutflowers</li><li>Vegetables</li><li>Soft fruit</li></ul>

  <h3 style="left:627px;top:141px">NEWS &amp; DOWNLOADS</h3>
  <h3 style="left:867px;top:141px">FREE DATA SETS</h3>
  <h3 style="left:627px;top:192px">CUSTOMER CASES</h3>
  <h3 style="left:867px;top:192px">CONTACT</h3>
</footer>

</body>
</html>
```